Computer consultant business card

Bexil Software is a newly started computer consulting company. It's a small one-man company that provides mostly Vornix applications but also websites in collaboration with designers. I'm running this company on the side of full time university studies.

I want the final design to be clean and memorable. Be creative! :)

Some inspiration:
http://www.pixelmarta.com/design/48317
http://www.pixelmarta.com/design/2739164/business-card-design-by-frostlynk
http://www.pixelmarta.com/design/604281/business-card-design-by-koralind-vestrabanu

See attachment for my company logo.
Updates

I would like to thank everyone for submitting! I'll need a couple of days to review and ultimately select a design.

Target Market(s)

Non-technical entrepreneurs and small companies.

Industry/Entity Type

University

Requirements
Must have
• My company logo.
In any way, both colors from my logo.
First- and last name, e-mail and phone number.
Double-sided design.
Nice to have
• Something creative with the symbol in my logo

```html
<!DOCTYPE html>
<html lang="en">
<head>
<meta charset="utf-8">
<title>Bexil Software – Business Card</title>
<link rel="stylesheet" href="https://fonts.googleapis.com/css2?family=Open+Sans:wght@400;600&family=Oswald:wght@500&display=swap">
<style>
  :root {
    --page-bg: #d9dadc;
    --card-light: #e7e9ec;
    --card-strip: #c9ccd0;
    --frame: #eceef0;
    --blue: #4a76b4;
    --blue-light: #6f98cc;
    --blue-dark: #3a63a3;
    --ink: #4a4a4c;
    --ink-soft: #6d6f73;
    --white: #ffffff;
  }
  * { margin: 0; padding: 0; box-sizing: border-box; }
  html, body { width: 1200px; height: 900px; overflow: hidden; }
  body {
    background: var(--page-bg);
    font-family: "Open Sans", Arial, sans-serif;
    display: flex;
    flex-direction: column;
    align-items: center;
    justify-content: center;
    gap: 40px;
  }
  .card {
    position: relative;
    width: 700px;
    height: 400px;
    overflow: hidden;
    box-shadow: 0 6px 18px rgba(0,0,0,0.18);
  }

  /* Back side: contact details */
  .card-back { background: var(--card-light); }
  .card-back .side-strip {
    position: absolute; left: 0; top: 0; bottom: 0; width: 62px;
    background: var(--card-strip);
  }
  .card-back .corner-block {
    position: absolute; right: 0; top: 0; width: 70px; height: 52px;
    background: var(--card-strip);
  }
  .card-back .accent-band {
    position: absolute; left: 62px; right: 0; top: 222px; height: 26px;
    background: var(--blue);
  }
  .card-back .brand {
    position: absolute; left: 112px; top: 138px;
    display: flex; align-items: center; gap: 16px;
  }
  .brand-dot { width: 46px; height: 46px; border-radius: 50%; background: var(--blue); }
  .brand-name {
    font-weight: 600; font-size: 62px; line-height: 1; letter-spacing: 1px;
    color: var(--ink);
  }
  .card-back .holder {
    position: absolute; right: 40px; top: 62px; text-align: right;
  }
  .holder-name {
    font-family: "Oswald", "Arial Narrow", sans-serif;
    font-weight: 500; font-size: 26px; line-height: 1; color: var(--blue);
  }
  .holder-role { font-size: 13px; color: var(--ink-soft); margin-top: 2px; }
  .card-back .contact {
    position: absolute; left: 112px; top: 268px;
    list-style: none; font-size: 16px; line-height: 28px; color: var(--ink);
  }

  /* Front side: logo panel */
  .card-front { background: var(--frame); padding: 44px; }
  .card-front .panel {
    width: 100%; height: 100%;
    background: radial-gradient(ellipse at 40% 35%, var(--blue-light) 0%, var(--blue) 55%, var(--blue-dark) 100%);
    display: flex; flex-direction: column; align-items: center; justify-content: center;
  }
  .card-front .brand { display: flex; align-items: center; gap: 16px; }
  .card-front .brand-dot { background: var(--white); }
  .card-front .brand-name { color: var(--ink); }
  .tagline {
    margin-top: 8px; margin-left: 60px;
    font-size: 17px; letter-spacing: 1px; color: var(--white);
  }
</style>
</head>
<body>
  <section class="card card-back">
    <div class="side-strip"></div>
    <div class="corner-block"></div>
    <div class="holder">
      <p class="holder-name">MIRA TOLVEN</p>
      <p class="holder-role">Graphic Designer</p>
    </div>
    <div class="brand">
      <span class="brand-dot"></span>
      <span class="brand-name">bexil</span>
    </div>
    <div class="accent-band"></div>
    <ul class="contact">
      <li>412 Marrowind Ave. Ostrel NY 60817</li>
      <li>Tel: 5550 1942 &nbsp;-&nbsp; Fax: 5550 1943</li>
      <li>Email: mira@bexilsoft.com</li>
    </ul>
  </section>

  <section class="card card-front">
    <div class="panel">
      <div class="brand">
        <span class="brand-dot"></span>
        <span class="brand-name">bexil</span>
      </div>
      <p class="tagline">tagline / slogan / website</p>
    </div>
  </section>
</body>
</html>
```